Business Card for a Dental Office

The design should communicate integrity, quality and reliability. We also want the card look elegant, simple, but still stand out, different from the traditional-dental-office business card.

Industry/Entity Type

Business

```html
<!DOCTYPE html>
<html lang="en">
<head>
<meta charset="utf-8">
<title>Harbourline Dental Studio – Business Card</title>
<link rel="stylesheet" href="https://fonts.googleapis.com/css2?family=Open+Sans:wght@400;700&display=swap">
<style>
  :root {
    --page-bg: #ececea;
    --card-bg: #ffffff;
    --ink: #111111;
    --ink-soft: #2a2a2a;
    --gold: #c9b21a;
    --gold-deep: #a8920f;
    --yellow: #f2e61c;
    --band-black: #050505;
    --rule: #222222;
  }
  * { box-sizing: border-box; margin: 0; padding: 0; }
  html, body {
    width: 1200px;
    height: 1000px;
    overflow: hidden;
    background: var(--page-bg);
    font-family: "Open Sans", Arial, sans-serif;
  }
  .card {
    position: absolute;
    left: 100px;
    top: 201px;
    width: 1000px;
    height: 597px;
    background: var(--card-bg);
    box-shadow: 0 6px 18px rgba(0,0,0,0.18);
    overflow: hidden;
  }
  .brand {
    position: absolute;
    left: 180px;
    top: 168px;
    display: flex;
    align-items: center;
    gap: 18px;
  }
  .brand-mark {
    width: 46px;
    height: 46px;
    background: var(--gold);
  }
  .brand-name {
    font-weight: 700;
    font-size: 46px;
    letter-spacing: 0.5px;
    color: var(--ink);
    line-height: 1;
    text-transform: uppercase;
  }
  .holder {
    position: absolute;
    right: 534px;
    top: 366px;
    text-align: right;
  }
  .holder-name {
    font-weight: 700;
    font-size: 30px;
    color: var(--ink);
    line-height: 1.2;
  }
  .holder-title {
    font-size: 22px;
    color: var(--ink-soft);
    line-height: 1.3;
  }
  .divider {
    position: absolute;
    left: 499px;
    top: 327px;
    width: 2px;
    height: 172px;
    background: var(--rule);
  }
  .contact {
    position: absolute;
    left: 531px;
    top: 322px;
    font-size: 22px;
    color: var(--ink-soft);
    line-height: 35px;
  }
  .contact-address { margin-bottom: 14px; }
  .contact-row {
    display: flex;
    align-items: center;
    gap: 14px;
  }
  .contact-row svg { width: 22px; height: 22px; flex: none; fill: var(--gold); }
  .band {
    position: absolute;
    left: 0;
    bottom: 0;
    width: 100%;
    height: 48px;
    background: linear-gradient(90deg, var(--band-black) 0%, var(--band-black) 45%, #6b6206 48%, var(--gold-deep) 55%, var(--yellow) 85%, #d9c915 100%);
  }
  .band-mark {
    position: absolute;
    left: 486px;
    top: 10px;
    width: 28px;
    height: 28px;
    background: var(--card-bg);
  }
</style>
</head>
<body>
  <main class="card">
    <div class="brand">
      <span class="brand-mark"></span>
      <span class="brand-name">Harbourline Dental Studio</span>
    </div>

    <div class="holder">
      <p class="holder-name">Elliot Marsh, PHA</p>
      <p class="holder-title">President</p>
    </div>

    <div class="divider"></div>

    <div class="contact">
      <p class="contact-address">Level 12, 48 Kestrel House<br>Sydney, New South Wales</p>
      <p class="contact-row">
        <svg viewBox="0 0 24 24" aria-hidden="true"><path d="M3 9c0-3 4-5 9-5s9 2 9 5v2h-5V9c-1-1-7-1-8 0v2H3zM6 13h12l2 7H4z"/></svg>
        <span>+ 000 000 0000</span>
      </p>
      <p class="contact-row">
        <svg viewBox="0 0 24 24" aria-hidden="true"><path d="M6 3h12v5H6zM3 9h18v8h-3v-3H6v3H3zM7 15h10v6H7z"/></svg>
        <span>+ 000 000 0000</span>
      </p>
      <p class="contact-row">
        <svg viewBox="0 0 24 24" aria-hidden="true"><path d="M2 6h20v1l-10 6L2 7zM2 9l10 6 10-6v9H2z"/></svg>
        <span>info@harbourlinedental.com</span>
      </p>
    </div>

    <div class="band"><span class="band-mark"></span></div>
  </main>
</body>
</html>
```